The Q Collective Business Cards

We need a sleek looking business card for our real estate company. Looking for a clean, modern, eye catching design on a standard size business card.
Updates

No more submissions please! Thank you!

Target Market(s)

General Public/Real Estate Clients

Industry/Entity Type

Real Estate

Contact Information for Business Card

Cards will be customized for each agent.

Colors

Designer to choose only greyscale colors for use in the design.

Requirements
Must have
• Black, white, gray color pallet, Photo area for headshot on the front of the card

```html
<!DOCTYPE html>
<html lang="en">
<head>
<meta charset="utf-8">
<title>The Q Collective – Agent Business Card</title>
<link rel="stylesheet" href="https://fonts.googleapis.com/css2?family=Roboto:ital,wght@0,400;0,500;1,400&display=swap">
<style>
  :root {
    --page-bg: #e4e2df;
    --card-bg: #f3f2f0;
    --ink: #1c1c1c;
    --band-black: #141414;
    --band-grey: #9a9a9a;
    --rule-grey: #c9c9c9;
    --name-light: #f1ebe2;
    --title-light: #d9d9d9;
    --photo-top: #8a6b55;
    --photo-mid: #b59a86;
    --photo-low: #d8cbbd;
  }
  html, body {
    margin: 0;
    width: 1200px;
    height: 1054px;
    overflow: hidden;
    background: var(--page-bg);
  }
  .business-card {
    position: absolute;
    left: 100px;
    top: 242px;
    width: 1000px;
    height: 570px;
    border-radius: 26px;
    overflow: hidden;
    background: var(--card-bg);
    box-shadow: 0 18px 40px rgba(0,0,0,0.18);
    font-family: "Roboto", Arial, sans-serif;
    color: var(--ink);
  }
  .headshot-area {
    position: absolute;
    left: 549px;
    top: 150px;
    width: 451px;
    height: 420px;
    background: linear-gradient(180deg, var(--photo-top) 0%, var(--photo-mid) 55%, var(--photo-low) 100%);
  }
  .header-band {
    position: absolute;
    inset: 0;
    width: 1000px;
    height: 570px;
  }
  .agent-name {
    position: absolute;
    right: 52px;
    top: 38px;
    margin: 0;
    font-weight: 500;
    font-size: 34px;
    color: var(--name-light);
  }
  .agent-title {
    position: absolute;
    right: 52px;
    top: 88px;
    margin: 0;
    font-style: italic;
    font-weight: 400;
    font-size: 23px;
    color: var(--title-light);
  }
  .brand {
    position: absolute;
    left: 43px;
    top: 222px;
    display: flex;
    align-items: center;
    gap: 16px;
  }
  .brand-square {
    width: 30px;
    height: 30px;
    background: var(--ink);
  }
  .brand-name {
    font-weight: 400;
    font-size: 40px;
    letter-spacing: 1px;
    color: var(--ink);
  }
  .address {
    position: absolute;
    left: 43px;
    top: 347px;
    margin: 0;
    font-style: normal;
    font-size: 24px;
    line-height: 38px;
  }
  .contact-list {
    position: absolute;
    left: 43px;
    top: 435px;
    margin: 0;
    padding: 0;
    list-style: none;
    font-size: 24px;
  }
  .contact-list li {
    display: flex;
    align-items: center;
    height: 38px;
  }
  .contact-icon {
    width: 22px;
    height: 22px;
    margin-right: 28px;
    fill: var(--ink);
  }
</style>
</head>
<body>
  <div class="business-card">
    <div class="headshot-area" role="img" aria-label="Agent headshot photo"></div>

    <svg class="header-band" viewBox="0 0 1000 570" aria-hidden="true">
      <polygon points="0,0 1000,0 1000,150 560,150 470,56 0,56" fill="var(--band-black)"/>
      <polygon points="0,66 466,66 556,160 1000,160 1000,168 552,168 462,74 0,74" fill="var(--band-grey)"/>
      <line x1="43" y1="300" x2="480" y2="300" stroke="var(--rule-grey)" stroke-width="2"/>
    </svg>

    <h1 class="agent-name">Maya Delgado Hart</h1>
    <p class="agent-title">Real Estate Broker</p>

    <div class="brand">
      <span class="brand-square"></span>
      <span class="brand-name">The Q Collective</span>
    </div>

    <address class="address">
      4218 Magnolia Ave<br>
      Riverton, LA, US 70942
    </address>

    <ul class="contact-list">
      <li>
        <svg class="contact-icon" viewBox="0 0 24 24" aria-hidden="true"><path d="M6.6 10.8a15 15 0 0 0 6.6 6.6l2.2-2.2a1 1 0 0 1 1-.25 11.4 11.4 0 0 0 3.6.57 1 1 0 0 1 1 1V20a1 1 0 0 1-1 1A17 17 0 0 1 3 4a1 1 0 0 1 1-1h3.5a1 1 0 0 1 1 1c0 1.25.2 2.45.57 3.57a1 1 0 0 1-.25 1z"/></svg>
        +1 555-201-7734
      </li>
      <li>
        <svg class="contact-icon" viewBox="0 0 24 24" aria-hidden="true"><path d="M2 5h20v14H2z M4 7v.5l8 5 8-5V7l-8 5z" fill-rule="evenodd"/></svg>
        maya@homeseekpro.com
      </li>
      <li>
        <svg class="contact-icon" viewBox="0 0 24 24" aria-hidden="true"><circle cx="12" cy="12" r="9" fill="none" stroke="var(--ink)" stroke-width="2"/><path d="M3 12h18M12 3c3 3 3 15 0 18M12 3c-3 3-3 15 0 18" fill="none" stroke="var(--ink)" stroke-width="1.6"/></svg>
        www.homeseekpro.com
      </li>
    </ul>
  </div>
</body>
</html>
```